Puffy Clouds Cotton Candy

Looking for a logo design and business cards to help a 13 year old entrepreneur promote her cotton candy business.
Contact Information for Business Card
Name, Phone & Email
Colors
E54698
E96AAD
F1A4CE
F9D9EA
FCEFF6
A7469A
B969AE
D3A5CF
EDDBEB
F8F0F9
6B429C
8869AF
B7A5CE
E3DAEB
F3F0F8
Requirements
Must have
- A fun feel that is appropriate for a teenage girl selling cotton candy

```html
<!DOCTYPE html>
<html lang="en">
<head>
<meta charset="utf-8">
<title>Puffy Clouds Cotton Candy – Business Cards</title>
<link rel="stylesheet" href="https://fonts.googleapis.com/css2?family=Fredoka:wght@600&family=Lato:wght@400;700&display=swap">
<style>
  :root {
    --pink: #E54698;
    --pink-soft: #E96AAD;
    --purple: #6B429C;
    --purple-mid: #8869AF;
    --magenta: #A7469A;
    --white: #FFFFFF;
    --backdrop: #1E1E1E;
  }
  * { margin: 0; padding: 0; box-sizing: border-box; }
  html, body {
    width: 1200px;
    height: 1015px;
    overflow: hidden;
    background: var(--backdrop);
  }
  .canvas {
    position: relative;
    width: 1200px;
    height: 1015px;
  }
  .card {
    position: absolute;
    left: 250px;
    width: 700px;
    height: 400px;
    overflow: hidden;
    box-shadow: 0 12px 30px rgba(0,0,0,0.55);
  }
  .card--front {
    top: 60px;
    background: linear-gradient(200deg, var(--purple-mid) 0%, var(--magenta) 40%, var(--pink) 85%);
  }
  .card--back {
    top: 545px;
    background: var(--white);
  }
  .brand {
    position: absolute;
    display: flex;
    flex-direction: column;
    align-items: center;
    font-family: "Fredoka", "Varela Round", sans-serif;
    font-weight: 600;
    text-align: center;
    line-height: 1.05;
  }
  .brand__dot {
    width: 92px;
    height: 92px;
    border-radius: 50%;
    margin-bottom: 18px;
  }
  .card--front .brand {
    left: 0; right: 0; top: 88px;
    color: var(--white);
  }
  .card--front .brand__dot { background: var(--white); }
  .card--front .brand__name { font-size: 46px; }
  .card--front .brand__tag { font-size: 32px; }

  .card--back .brand {
    left: 60px; top: 48px;
    color: var(--pink);
  }
  .card--back .brand__dot { background: var(--pink); width: 84px; height: 84px; margin-bottom: 14px; }
  .card--back .brand__name { font-size: 40px; }
  .card--back .brand__tag { font-size: 28px; }

  .wave {
    position: absolute;
    inset: 0;
    width: 700px;
    height: 400px;
  }
  .contact {
    position: absolute;
    right: 40px;
    top: 205px;
    text-align: right;
    color: var(--white);
    font-family: "Lato", sans-serif;
  }
  .contact__name {
    font-family: "Fredoka", "Varela Round", sans-serif;
    font-weight: 600;
    font-size: 30px;
    line-height: 1.1;
  }
  .contact__role {
    font-size: 18px;
    margin-bottom: 22px;
  }
  .contact__line {
    display: flex;
    justify-content: flex-end;
    align-items: center;
    gap: 8px;
    font-size: 19px;
    line-height: 1.55;
  }
  .contact__icon { width: 18px; height: 18px; }
</style>
</head>
<body>
<main class="canvas">

  <section class="card card--front" aria-label="Business card front">
    <div class="brand">
      <span class="brand__dot"></span>
      <span class="brand__name">Puffy Clouds</span>
      <span class="brand__tag">Cotton Candy</span>
    </div>
  </section>

  <section class="card card--back" aria-label="Business card back">
    <svg class="wave" viewBox="0 0 700 400" aria-hidden="true">
      <path d="M0,352 C210,352 270,300 370,195 C450,112 540,72 700,62 L700,400 L0,400 Z" fill="var(--pink)"/>
      <path d="M0,336 C200,336 262,286 360,180 C440,96 540,56 700,46" fill="none" stroke="var(--purple)" stroke-width="9"/>
      <path d="M0,362 C215,362 280,310 378,205 C455,124 545,82 700,72" fill="none" stroke="var(--white)" stroke-width="4"/>
    </svg>

    <div class="brand">
      <span class="brand__dot"></span>
      <span class="brand__name">Puffy Clouds</span>
      <span class="brand__tag">Cotton Candy</span>
    </div>

    <div class="contact">
      <p class="contact__name">Lily Carter</p>
      <p class="contact__role">Managing Director</p>
      <p class="contact__line">044-555 010 234
        <svg class="contact__icon" viewBox="0 0 24 24" aria-hidden="true"><path fill="var(--white)" d="M6.6 10.8a15.1 15.1 0 0 0 6.6 6.6l2.2-2.2c.3-.3.7-.4 1-.2 1.1.4 2.3.6 3.6.6.6 0 1 .4 1 1V20c0 .6-.4 1-1 1A17 17 0 0 1 3 4c0-.6.4-1 1-1h3.5c.6 0 1 .4 1 1 0 1.3.2 2.5.6 3.6.1.3 0 .7-.2 1z"/></svg>
      </p>
      <p class="contact__line">hello@puffyclouds.com
        <svg class="contact__icon" viewBox="0 0 24 24" aria-hidden="true"><path fill="var(--white)" d="M2 5h20v14H2z"/><path fill="none" stroke="var(--pink)" stroke-width="1.8" d="M2.5 5.5l9.5 8 9.5-8"/></svg>
      </p>
    </div>
  </section>

</main>
</body>
</html>
```